Presentation Of Our Epidemiology Consulting Framework

We need a slide deck (png files) for PowerPoint that describes our organization and type of clients we serve, and our 6 phase framework that explains how we work with clients. Please use the minimum amount of text on each slide.  We want a more visual display of how to work with us. We want it to look very similar to our brochure.  We want to also have a few extra branded slides without text that can be used as a template if we decide to add to the deck later or create a new slide deck.
Colors
#56588C
#F28444
#F2E088
#F24C27
#ODODOD

```html
<!DOCTYPE html>
<html lang="en">
<head>
<meta charset="utf-8">
<title>DrRVance Framework Deck</title>
<link href="https://fonts.googleapis.com/css2?family=Montserrat:wght@400;500;600;700;800&display=swap" rel="stylesheet">
<style>
:root{
  --navy:#2f2f5c;
  --purple:#56588C;
  --purple-deep:#3d3e72;
  --orange:#F28444;
  --orange-hot:#F24C27;
  --ink:#0D0D0D;
  --text:#2b2b3a;
  --page:#e8e8f1;
  --white:#ffffff;
}
*{box-sizing:border-box;margin:0;padding:0}
html,body{width:1200px;height:4147px;overflow:hidden}
body{background:var(--page);font-family:"Montserrat",sans-serif;color:var(--text);position:relative}
.slide{position:absolute;left:44px;width:1112px;height:625px;overflow:hidden;background:var(--white);box-shadow:0 6px 18px rgba(40,40,80,.18)}
.slide--dark{background:linear-gradient(100deg,#2c2c58 0%,#3f4078 55%,#5a5c94 100%);color:var(--white)}
.brand{position:absolute;font-weight:700;color:var(--orange);white-space:nowrap;letter-spacing:-.5px}
.brand--hero{left:50px;top:112px;font-size:50px;line-height:60px}
.brand--foot{left:48px;top:570px;font-size:27px;line-height:32px;color:var(--purple)}
.footer-line{position:absolute;left:287px;top:586px;width:748px;height:2px;background:var(--purple)}
.page-no{position:absolute;left:1032px;top:568px;width:36px;height:36px;border-radius:50%;background:var(--purple-deep);color:var(--white);font-size:12px;font-weight:700;display:flex;align-items:center;justify-content:center}
.hero-title{position:absolute;left:44px;top:228px;font-size:46px;line-height:47px;font-weight:800}
.hero-title .accent{color:var(--orange)}
.hero-sub{position:absolute;left:44px;top:378px;font-size:32px;font-weight:500}
.pill{position:absolute;left:0;top:472px;height:64px;border-radius:0 34px 34px 0;background:linear-gradient(90deg,var(--orange-hot),var(--orange) 60%,#f6a35f);display:flex;align-items:center;padding-left:48px;gap:14px;font-size:18px;font-weight:700;color:var(--white);box-shadow:6px 6px 0 rgba(0,0,0,.25)}
.photo{position:absolute}
.photo--portrait{left:610px;top:74px;width:440px;height:476px;border-radius:48% 48% 44% 44%/40% 40% 60% 60%;background:radial-gradient(circle at 50% 40%,#8a6b5a 0%,#4a4a6e 55%,#3a3b70 100%)}
.photo--nurse{left:0;top:0;width:600px;height:540px;clip-path:polygon(0 0,330px 0,570px 240px,300px 540px,0 540px);background:linear-gradient(135deg,#d9e3ee,#6fa6d6 55%,#3f7fbe)}
.photo-frame{position:absolute;left:0;top:0}
.agenda-title{position:absolute;left:625px;top:88px;font-size:44px;font-weight:700;color:var(--purple)}
.rule{position:absolute;width:34px;height:3px;background:var(--orange)}
.agenda-list{position:absolute;left:625px;top:170px;list-style:none}
.agenda-list li{font-size:21px;line-height:46px;color:var(--purple-deep);font-weight:500}
.agenda-list b{font-weight:700}
.phase-title{position:absolute;left:50px;top:38px;font-size:42px;line-height:47px;font-weight:800;color:var(--purple)}
.phase-title .num{color:var(--orange)}
.phase-sub{position:absolute;left:49px;font-size:25px;font-weight:500;color:var(--text)}
.cards{position:absolute;left:48px;top:293px;display:flex;gap:36px}
.card{position:relative;width:227px;height:192px;border-radius:14px;padding:58px 22px 0;font-size:16px;line-height:26px;color:#555}
.card--warm{border:2px solid var(--orange);background:linear-gradient(135deg,#fff 40%,#fde6d6)}
.card--cool{border:2px solid var(--purple);background:linear-gradient(135deg,#fff 35%,#d9daf0)}
.card-icon{position:absolute;top:-28px;left:50%;margin-left:-28px;width:56px;height:56px;border-radius:50%;background:var(--white);box-shadow:0 3px 8px rgba(0,0,0,.15);display:flex;align-items:center;justify-content:center}
.steps{position:absolute;left:0;top:224px;width:700px}
.step{position:absolute;height:56px;border-radius:28px 0 0 28px;display:flex;align-items:center;padding-left:32px;font-size:16px;font-weight:500;color:var(--white);right:0}
.photo--team{left:601px;top:0;width:511px;height:537px;border-radius:0 0 0 60px;background:linear-gradient(135deg,#1f2a44,#3b4f74 50%,#8894a8)}
.lead-note{position:absolute;left:49px;top:367px;font-size:14px;color:#555}
.task-list{position:absolute;left:596px;top:139px;width:470px;list-style:none}
.task{height:72px;margin-bottom:16px;border-radius:14px;background:var(--white);box-shadow:0 4px 14px rgba(60,60,110,.14);display:flex;align-items:center;padding:0 40px;font-size:15px;font-weight:600;color:var(--ink)}
.task--tall{height:92px}
.cta-copy{position:absolute;left:44px;top:380px;font-size:17px;line-height:30px;font-weight:500}
.glow{position:absolute;left:640px;top:90px;width:450px;height:450px;border-radius:50%;background:radial-gradient(circle,rgba(242,132,68,.18),rgba(86,88,140,0) 70%)}
</style>
</head>
<body>

<section class="slide slide--dark" style="top:55px">
  <div class="brand brand--hero">Dr RVance</div>
  <h1 class="hero-title">Transforming Health<br>Data into <span class="accent">Community</span><br><span class="accent">Impact:</span></h1>
  <p class="hero-sub">The DrRVance Framework</p>
  <div class="pill" style="width:375px">
    <svg width="18" height="18" viewBox="0 0 18 18" fill="none" stroke="#fff" stroke-width="1.8"><rect x="2" y="3.5" width="14" height="12.5" rx="2"/><path d="M2 7.5h14M6 1.5v4M12 1.5v4"/></svg>
    23 January 2025
  </div>
  <div class="photo photo--portrait" role="img" aria-label="Portrait photo of the consultant smiling, in a dark blazer and glasses"></div>
</section>

<section class="slide" style="top:734px">
  <div class="photo photo--nurse" role="img" aria-label="Photo of a nurse in blue scrubs reading a tablet"></div>
  <svg class="photo-frame" width="620" height="560" viewBox="0 0 620 560"><path d="M340 0 L585 245 L320 540 L295 540 L560 245 L315 0Z" fill="#56588C"/></svg>
  <h2 class="agenda-title">Agenda</h2>
  <div class="rule" style="left:627px;top:148px"></div>
  <ul class="agenda-list">
    <li><b>Phase 1:</b> Discovery &amp; Vision Alignment</li>
    <li><b>Phase 2:</b> Partnership Launch</li>
    <li><b>Phase 3:</b> Expert Execution</li>
    <li><b>Phase 4:</b> Collaborative Refinement</li>
    <li><b>Phase 5:</b> Impact Delivery</li>
    <li><b>Phase 6:</b> Evolution &amp; Growth</li>
    <li><b>Why Partner With Us?</b></li>
  </ul>
  <div class="brand brand--foot">Dr RVance</div><div class="footer-line"></div><div class="page-no">02</div>
</section>

<section class="slide" style="top:1413px">
  <h2 class="phase-title"><span class="num">Phase 1:</span><br>Discovery &amp; Vision Alignment</h2>
  <div class="rule" style="left:52px;top:150px"></div>
  <p class="phase-sub" style="top:170px">Building the Foundation for Success</p>
  <div class="cards">
    <div class="card card--warm"><div class="card-icon"><svg width="26" height="26" viewBox="0 0 26 26"><circle cx="13" cy="13" r="8" fill="none" stroke="#F28444" stroke-width="5" stroke-dasharray="4 2.3"/><circle cx="13" cy="13" r="4" fill="#F28444"/></svg></div>Deep-dive exploration of your organization's unique challenges and opportunities</div>
    <div class="card card--warm"><div class="card-icon"><svg width="26" height="26" viewBox="0 0 26 26" fill="#F28444"><rect x="11.5" y="2" width="3" height="22" rx="1.5"/><rect x="5" y="6" width="16" height="5" rx="2"/><rect x="6" y="14" width="14" height="5" rx="2"/></svg></div>Strategic alignment of goals and expectations</div>
    <div class="card card--cool"><div class="card-icon"><svg width="26" height="26" viewBox="0 0 26 26" stroke="#56588C" stroke-width="2.4" fill="#56588C"><path d="M3 6h20M3 13h20M3 20h20"/><circle cx="9" cy="6" r="2.5"/><circle cx="17" cy="13" r="2.5"/><circle cx="8" cy="20" r="2.5"/></svg></div>Custom-tailored solution design</div>
    <div class="card card--cool"><div class="card-icon"><svg width="28" height="26" viewBox="0 0 28 26" fill="#56588C"><rect x="3" y="16" width="5" height="8"/><rect x="10" y="12" width="5" height="12"/><rect x="17" y="14" width="5" height="10"/><rect x="21" y="2" width="1.8" height="12"/><path d="M22.8 2h4l-1.4 2.5 1.4 2.5h-4z"/></svg></div>Clear roadmap development with defined milestones</div>
  </div>
  <div class="brand brand--foot">Dr RVance</div><div class="footer-line"></div><div class="page-no">03</div>
</section>

<section class="slide" style="top:2092px">
  <h2 class="phase-title"><span class="num">Phase 2:</span><br>Partnership Launch</h2>
  <div class="rule" style="left:52px;top:150px"></div>
  <p class="phase-sub" style="top:170px">Setting the Stage for Excellence</p>
  <div class="steps">
    <div class="step" style="left:48px;top:0;background:linear-gradient(90deg,#f5894a,#f47a3a)">Formation of dedicated project team</div>
    <div class="step" style="left:71px;top:64px;background:linear-gradient(90deg,#f47c3c,#f36a30)">Establishment of collaborative workflow</div>
    <div class="step" style="left:94px;top:128px;background:linear-gradient(90deg,#f36f33,#f25e2b)">Comprehensive data gathering</div>
    <div class="step" style="left:117px;top:192px;background:linear-gradient(90deg,#f2632d,#f25227)">Strategic timeline planning</div>
    <div class="step" style="left:140px;top:256px;background:linear-gradient(90deg,#f25428,#e8431f)">Stakeholder engagement and vision capture</div>
  </div>
  <div class="photo photo--team" role="img" aria-label="Photo of two clinicians reviewing data on a tablet"></div>
  <div class="brand brand--foot">Dr RVance</div><div class="footer-line"></div><div class="page-no">04</div>
</section>

<section class="slide" style="top:2771px">
  <h2 class="phase-title" style="top:196px"><span class="num">Phase 3:</span><br>Expert Execution</h2>
  <div class="rule" style="left:52px;top:309px"></div>
  <p class="phase-sub" style="top:328px">Where Science Meets Service</p>
  <p class="lead-note">Our specialized team begins the transformation process:</p>
  <ol class="task-list">
    <li class="task">1.&nbsp; In-depth research and analysis</li>
    <li class="task">2.&nbsp; Content development and refinement</li>
    <li class="task">3.&nbsp; Data interpretation and visualization</li>
    <li class="task task--tall">4.&nbsp; Plain language translation of complex health<br>&nbsp;&nbsp;&nbsp;&nbsp;&nbsp;information</li>
  </ol>
  <div class="brand brand--foot">Dr RVance</div><div class="footer-line"></div><div class="page-no">05</div>
</section>

<section class="slide slide--dark" style="top:3450px">
  <div class="brand brand--hero">Dr RVance</div>
  <h2 class="hero-title" style="top:220px">Ready to Transform<br>Your <span class="accent">Health</span><br><span class="accent">Communication?</span></h2>
  <p class="cta-copy">Contact us to begin your journey toward more effective,<br>equitable health communication</p>
  <div class="pill" style="width:411px">
    <svg width="18" height="14" viewBox="0 0 18 14"><rect width="18" height="14" rx="2" fill="#fff"/><path d="M1 1.5l8 6 8-6" fill="none" stroke="#F28444" stroke-width="1.6"/></svg>
    support@drrvance.com
  </div>
  <div class="glow"></div>
</section>

</body>
</html>
```